Business Card Design for company

We want new business cards. We'd like something different-- yet still highly professional. Our tagline is Providing leadership, delivering success. Stock photos are ok, as long as they are relevant and look upscale.

Target Market(s)

Architecture/Business Management Consulting/Engineering Consulting

Contact Information for Business Card

dark gray background with pops of blue might be good, but you tell me. You're the designers. Rounded corners might be nice, but again, you tell me.

Font styles to use
Serif
Sans Serif

Colors
3276b5
5c5c5c
9d9d9d
fbfbfb

Requirements
Nice to have
• Something different, but still very professional.

```html
<!DOCTYPE html>
<html lang="en">
<head>
<meta charset="utf-8">
<title>Halvard Consulting – Business Card</title>
<link rel="stylesheet" href="https://fonts.googleapis.com/css2?family=Roboto:wght@400;500;700&display=swap">
<style>
  :root {
    --page-bg: #2b2b2d;
    --brand-blue: #286296;
    --card-white: #ffffff;
    --slate: #4a4c51;
    --text-light: #ffffff;
  }
  * { box-sizing: border-box; margin: 0; padding: 0; }
  html, body {
    width: 1125px;
    height: 1200px;
    overflow: hidden;
    background: var(--page-bg);
    font-family: "Roboto", Arial, sans-serif;
  }
  .card {
    position: absolute;
    left: 150px;
    width: 826px;
    height: 471px;
    overflow: hidden;
  }
  .card--front { top: 98px; background: var(--card-white); }
  .card--back { top: 631px; background: var(--slate); }

  .contact-panel {
    position: absolute;
    left: 0; top: 0;
    width: 358px;
    height: 100%;
    background: var(--brand-blue);
    color: var(--text-light);
  }
  .person-name {
    position: absolute;
    left: 39px; top: 90px;
    font-size: 30px;
    font-weight: 700;
    letter-spacing: 0.2px;
  }
  .person-title {
    position: absolute;
    left: 40px; top: 124px;
    font-size: 19.5px;
    font-weight: 700;
  }
  .address {
    position: absolute;
    left: 39px; top: 176px;
    font-size: 19.5px;
    line-height: 25px;
  }
  .contact-list {
    position: absolute;
    left: 39px; top: 241px;
    list-style: none;
    font-size: 19.5px;
  }
  .contact-list li {
    display: flex;
    align-items: center;
    height: 26.3px;
  }
  .contact-list svg {
    width: 19px; height: 19px;
    margin-right: 13px;
    fill: var(--text-light);
    flex: none;
  }

  .brand-panel {
    position: absolute;
    left: 358px; top: 0;
    width: 468px; height: 100%;
    display: flex;
    align-items: center;
    justify-content: center;
  }
  .brand-name {
    color: var(--brand-blue);
    font-size: 50px;
    font-weight: 500;
    line-height: 58px;
    letter-spacing: 3px;
    text-align: center;
  }

  .brand-name--back {
    position: absolute;
    left: 0; right: 0; top: 172px;
    text-align: center;
    color: var(--text-light);
    font-size: 122px;
    line-height: 122px;
    font-weight: 500;
    letter-spacing: 4px;
  }
  .tagline {
    position: absolute;
    left: 0; right: 0; top: 396px;
    text-align: center;
    color: var(--text-light);
    font-size: 20px;
  }
  .tagline .dot {
    display: inline-block;
    width: 7px; height: 7px;
    border-radius: 50%;
    background: var(--text-light);
    margin: 0 11px 3px;
  }
</style>
</head>
<body>
  <section class="card card--front">
    <div class="contact-panel">
      <h1 class="person-name">DANIEL REYES</h1>
      <p class="person-title">CEO/FOUNDER</p>
      <p class="address">2140 Cedar Hollow Road<br>Fairbanks, Alaska 99701</p>
      <ul class="contact-list">
        <li>
          <svg viewBox="0 0 24 24" aria-hidden="true"><path d="M6.6 10.8a15.1 15.1 0 0 0 6.6 6.6l2.2-2.2a1 1 0 0 1 1-.25 11.4 11.4 0 0 0 3.6.57 1 1 0 0 1 1 1V20a1 1 0 0 1-1 1A17 17 0 0 1 3 4a1 1 0 0 1 1-1h3.5a1 1 0 0 1 1 1c0 1.25.2 2.45.57 3.57a1 1 0 0 1-.25 1z"/></svg>
          555 214 7730
        </li>
        <li>
          <svg viewBox="0 0 24 24" aria-hidden="true"><path d="M8 1h8a2 2 0 0 1 2 2v18a2 2 0 0 1-2 2H8a2 2 0 0 1-2-2V3a2 2 0 0 1 2-2zm0 3v14h8V4zm4 15.5a1.2 1.2 0 1 0 0 2.4 1.2 1.2 0 0 0 0-2.4z"/></svg>
          555 382 1946
        </li>
        <li>
          <svg viewBox="0 0 24 24" aria-hidden="true"><path d="M6 2h12v6H6zM3 9h18a2 2 0 0 1 2 2v7h-4v4H5v-4H1v-7a2 2 0 0 1 2-2zm4 7v4h10v-4z"/></svg>
          555 607 3158
        </li>
        <li>
          <svg viewBox="0 0 24 24" aria-hidden="true"><path d="M2 5h20v2l-10 6L2 7zm0 4.3 10 6 10-6V19H2z"/></svg>
          daniel@halvardco.com
        </li>
        <li>
          <svg viewBox="0 0 24 24" aria-hidden="true"><path d="M12 2a10 10 0 1 0 0 20 10 10 0 0 0 0-20zm-1 17.9A8 8 0 0 1 4.2 10L9 14.8v1a2 2 0 0 0 2 2zm6.9-2.5A2 2 0 0 0 16 16h-1v-3a1 1 0 0 0-1-1H8v-2h2a1 1 0 0 0 1-1V7h2a2 2 0 0 0 2-2v-.4a8 8 0 0 1 2.9 12.8z"/></svg>
          www.halvardco.com
        </li>
      </ul>
    </div>
    <div class="brand-panel">
      <p class="brand-name">HALVARD<br>CONSULTING</p>
    </div>
  </section>

  <section class="card card--back">
    <p class="brand-name--back">HALVARD</p>
    <p class="tagline">Guiding every project<span class="dot"></span>building lasting value</p>
  </section>
</body>
</html>
```